Fresh, modern, fun business card for pediatric dental practice

Need a business card for fresh, modern, fun pediatric dental practice

Clean look that matches our website's font and colors

We prefer the look of curved corners on business cards

Target Market(s)

parents (mothers) of young children, professionals, mid-high class

Industry/Entity Type

Dental

Contact Information for Business Card

Maplebrook Pediatric Dentistry
482 Quarry Lane
Suite 517
Alder Falls, PA 17990
717.555.0193
www.maplebrookkidsdental.example

Mei-Ran Tsai, DMD
Corinne Walbeck, DMD
(we are working on our email address, but we would like that on the card as well)

Font styles to use
Sans Serif

Requirements
Must have
• All info; we would also like to make cards for individual staff members
• colors from our website and color palatte, attatched
• use same font and design as website for branding
Nice to have
• clean, simple card that has a pop of color
• we would like to see a few designs with our tag line "where smiles get brighter"
• we are not sure if we want to have it on there or not
• we would like to see a few designs incorporating the ribbon graphic on our website where the word WELCOME is

```html
<!DOCTYPE html>
<html lang="en">
<head>
<meta charset="utf-8">
<title>Maplebrook Pediatric Dentistry – Business Card</title>
<link rel="stylesheet" href="https://fonts.googleapis.com/css2?family=Ubuntu:wght@500;700&family=Roboto:wght@400&display=swap">
<style>
  :root {
    --plum: #4b2d4a;
    --gold: #e0a00f;
    --magenta: #b0287a;
    --paper: #f7f7f6;
    --ink: #333333;
    --stage: #e4e4e4;
    --soft-white: #ecebee;
  }
  * { margin: 0; padding: 0; box-sizing: border-box; }
  html, body { width: 1200px; height: 576px; overflow: hidden; }
  body { background: var(--stage); position: relative; font-family: "Roboto", Arial, sans-serif; }

  .card {
    position: absolute;
    top: 138px;
    height: 294px;
    border-radius: 14px;
    overflow: hidden;
  }

  /* Front */
  .card-front { left: 82px; width: 484px; background: var(--plum); }
  .front-brand { position: absolute; left: 0; right: 0; top: 52px; text-align: center; }
  .brand-dot {
    display: block; margin: 0 auto 14px;
    width: 44px; height: 44px; border-radius: 50%;
    background: var(--gold);
  }
  .brand-name {
    font-family: "Ubuntu", Arial, sans-serif;
    font-weight: 500;
    color: var(--gold);
    line-height: 1;
    text-transform: lowercase;
  }
  .front-brand .brand-line1 { font-size: 40px; display: block; }
  .front-brand .brand-line2 { font-size: 22px; display: block; margin-top: 6px; letter-spacing: 0.5px; }

  .front-web {
    position: absolute; left: 0; right: 0; top: 266px;
    display: flex; justify-content: center; align-items: center; gap: 20px;
    font-size: 12px; color: var(--soft-white); letter-spacing: 0.4px;
  }
  .front-web .domain { color: var(--gold); }
  .web-rule { width: 48px; height: 2px; background: linear-gradient(90deg, transparent, var(--magenta), transparent); }

  /* Back */
  .card-back { left: 602px; width: 481px; background: var(--paper); }
  .side-band { position: absolute; left: 0; top: 0; bottom: 0; width: 40px; }
  .side-band .band-top { height: 144px; background: var(--magenta); }
  .side-band .band-bottom { height: 150px; background: var(--plum); }
  .side-rule { position: absolute; left: 40px; top: 0; bottom: 0; width: 5px; background: var(--gold); }

  .back-brand { position: absolute; left: 78px; top: 40px; display: flex; align-items: center; gap: 16px; }
  .back-brand .brand-dot { margin: 0; width: 40px; height: 40px; }
  .back-brand .brand-line1 { font-size: 32px; display: block; }
  .back-brand .brand-line2 { font-size: 19px; display: block; margin-top: 3px; letter-spacing: 0.4px; }

  .person-name {
    position: absolute; left: 79px; top: 148px;
    font-family: "Ubuntu", Arial, sans-serif; font-weight: 700;
    font-size: 16px; color: var(--gold);
  }
  .address { position: absolute; left: 79px; top: 176px; font-size: 12.5px; line-height: 17px; color: var(--ink); font-style: normal; }
  .contact-list { position: absolute; left: 79px; top: 216px; list-style: none; font-size: 12.5px; color: var(--ink); }
  .contact-list li { display: flex; align-items: center; gap: 9px; height: 17px; }
  .contact-list svg { width: 10px; height: 10px; fill: var(--magenta); flex: none; }
  .contact-list .domain { color: var(--magenta); }
</style>
</head>
<body>

<section class="card card-front" aria-label="Business card front">
  <div class="front-brand">
    <span class="brand-dot" aria-hidden="true"></span>
    <p class="brand-name">
      <span class="brand-line1">Maplebrook</span>
      <span class="brand-line2">Pediatric Dentistry</span>
    </p>
  </div>
  <div class="front-web">
    <span class="web-rule" aria-hidden="true"></span>
    <span>www.<span class="domain">maplebrookkidsdental</span>.example</span>
    <span class="web-rule" aria-hidden="true"></span>
  </div>
</section>

<section class="card card-back" aria-label="Business card back">
  <div class="side-band" aria-hidden="true">
    <div class="band-top"></div>
    <div class="band-bottom"></div>
  </div>
  <div class="side-rule" aria-hidden="true"></div>

  <div class="back-brand">
    <span class="brand-dot" aria-hidden="true"></span>
    <p class="brand-name">
      <span class="brand-line1">Maplebrook</span>
      <span class="brand-line2">Pediatric Dentistry</span>
    </p>
  </div>

  <h1 class="person-name">Corinne Walbeck, DMD</h1>
  <address class="address">482 Quarry Lane<br>Suite 517 Alder Falls, PA 17990</address>

  <ul class="contact-list">
    <li>
      <svg viewBox="0 0 10 10" aria-hidden="true"><path d="M1 3c0-1.2 1.8-2 4-2s4 .8 4 2v1H7V3H3v1H1z M2 5h6l1 4H1z"/></svg>
      717.555.0193
    </li>
    <li>
      <svg viewBox="0 0 10 10" aria-hidden="true"><path d="M0 2h10v6H0z" /><path d="M0 2l5 3.5L10 2" fill="none" stroke="#f7f7f6" stroke-width="1"/></svg>
      name@maplebrookkidsdental.example
    </li>
    <li>
      <svg viewBox="0 0 10 10" aria-hidden="true"><circle cx="5" cy="5" r="4.5"/><path d="M0.5 5h9M5 0.5c-2 2.5-2 6.5 0 9M5 0.5c2 2.5 2 6.5 0 9" fill="none" stroke="#f7f7f6" stroke-width="0.7"/></svg>
      <span>www.<span class="domain">maplebrookkidsdental</span>.example</span>
    </li>
  </ul>
</section>

</body>
</html>
```